Hvac and insulation company needs good looking business card design

We are hvac and insulation company and looking for a new business cards that look to today standards designs

Target Market(s)

homeowners

Industry/Entity Type

Hvac

Contact Information for Business Card

Name: Walter Brinoku
Home comfort consultant
address: 4827 Dunmore St #215 Oakland, CA 94619
office: 888-316-2790
cell: 510-742-3185
Lic.# 584261
Email: walter@corvane-hvac.com
Web: corvane-hvac.com

Requirements
Must have
• clean and sleek look
Nice to have
• simple with a clean look
Should not have
• to busy business card

```html
<!DOCTYPE html>
<html lang="en">
<head>
<meta charset="utf-8">
<title>Corvane Home Solutions — Business Card</title>
<link href="https://fonts.googleapis.com/css2?family=Arimo:wght@400;700&display=swap" rel="stylesheet">
<style>
  :root {
    --backdrop: #3b3431;
    --card: #0d0d0d;
    --accent: #f5861f;
    --text-light: #c9c9c9;
    --text-dim: #9a9a9a;
    --silver: #d9d9d9;
    --divider: #3a3a3a;
  }
  * { margin: 0; padding: 0; box-sizing: border-box; }
  html, body { width: 1200px; height: 844px; overflow: hidden; }
  body {
    background: var(--backdrop);
    font-family: "Arimo", Arial, sans-serif;
    position: relative;
  }
  .card {
    position: absolute;
    top: 267px;
    width: 540px;
    height: 310px;
    background: var(--card);
    box-shadow: 0 14px 30px rgba(0,0,0,.45);
  }
  .card--front { left: 50px; }
  .card--back { left: 610px; }

  /* front */
  .brand-panel {
    position: absolute;
    left: 0; top: 0;
    width: 270px; height: 100%;
    display: flex;
    align-items: center;
    justify-content: center;
    gap: 12px;
  }
  .brand-mark {
    width: 34px; height: 34px;
    background: var(--accent);
  }
  .brand-name {
    color: var(--accent);
    font-weight: 700;
    font-size: 38px;
    letter-spacing: -0.5px;
  }
  .divider {
    position: absolute;
    left: 270px; top: 24px;
    width: 1px; height: 262px;
    background: var(--divider);
  }
  .contact-panel {
    position: absolute;
    left: 292px; top: 52px;
    color: var(--text-light);
    font-size: 13.5px;
    line-height: 1.35;
  }
  .person-name {
    color: var(--accent);
    font-weight: 700;
    font-size: 21px;
    line-height: 1.1;
  }
  .person-title { color: var(--text-dim); font-size: 13.5px; margin-bottom: 10px; }
  .license { margin-bottom: 8px; }
  .license-label { color: var(--accent); }
  .contact-list { list-style: none; margin-bottom: 12px; }
  .contact-list li { display: flex; align-items: center; gap: 8px; }
  .contact-icon { width: 11px; height: 11px; flex: none; fill: var(--accent); }
  .address { color: var(--text-light); }

  /* back */
  .back-brand {
    position: absolute;
    left: 0; top: 0; width: 100%; height: 100%;
    display: flex;
    align-items: center;
    justify-content: center;
    gap: 14px;
  }
  .back-mark { width: 44px; height: 44px; background: var(--silver); }
  .back-wordmark { display: flex; flex-direction: column; }
  .back-name {
    color: var(--silver);
    font-weight: 700;
    font-size: 44px;
    line-height: 1;
    letter-spacing: -0.5px;
  }
  .back-tagline {
    color: var(--text-dim);
    font-size: 12px;
    letter-spacing: 3px;
    margin-top: 4px;
  }
</style>
</head>
<body>
  <section class="card card--front">
    <div class="brand-panel">
      <span class="brand-mark"></span>
      <span class="brand-name">corvane</span>
    </div>
    <div class="divider"></div>
    <div class="contact-panel">
      <p class="person-name">Walter Brinoku</p>
      <p class="person-title">Home Comfort Consultant</p>
      <p class="license"><span class="license-label">LIC</span> # 584261</p>
      <ul class="contact-list">
        <li><svg class="contact-icon" viewBox="0 0 12 12"><path d="M2.5 0.5 L4.5 3 L3.5 4.5 Q4.8 7 7.5 8.5 L9 7.5 L11.5 9.5 L10 11.5 Q4.5 11 0.5 2 Z"/></svg>888-316-2790</li>
        <li><svg class="contact-icon" viewBox="0 0 12 12"><path d="M3 0 H9 V12 H3 Z M4 1.5 V9 H8 V1.5 Z M5.5 10 H6.5 V11 H5.5 Z" fill-rule="evenodd"/></svg>510-742-3185</li>
        <li><svg class="contact-icon" viewBox="0 0 12 12"><path d="M0 2 H12 V10 H0 Z M1 3 L6 6.5 L11 3 Z" fill-rule="evenodd"/></svg>walter@corvane-hvac.com</li>
        <li><svg class="contact-icon" viewBox="0 0 12 12"><path d="M6 0 A6 6 0 1 0 6.01 0 Z M6 2 A4 4 0 0 1 10 6 H6 Z" fill-rule="evenodd"/></svg>www.corvane-hvac.com</li>
      </ul>
      <p class="address">4827 Dunmore St<br>#215 Oakland, CA 94619</p>
    </div>
  </section>

  <section class="card card--back">
    <div class="back-brand">
      <span class="back-mark"></span>
      <div class="back-wordmark">
        <span class="back-name">corvane</span>
        <span class="back-tagline">home solutions</span>
      </div>
    </div>
  </section>
</body>
</html>
```